Halvery Construction Group Website

Need a dynamic corporate website that can be built on with time. We want to get our information out to the world and have a place where customers can submit requests for proposals.

Target Market(s)

Custom home owners and buyers. Architects and Real Estate Agents.

Industry/Entity Type

Construction

Number of Pages Required

3 page

Font styles to use
Serif
Sans Serif

Requirements
Must have
• Company logo, about, company contact information, biography, contact, projects,
• Sleek, modern, clean, attractive design.
• Online form customers can use for filling out a request for project proposal.
• Linkedin hyperlink.
• Uses www.halveryconstructiongroup.example

```html
<!DOCTYPE html>
<html lang="en">
<head>
<meta charset="utf-8">
<title>Halvery Construction Group</title>
<link rel="stylesheet" href="https://fonts.googleapis.com/css2?family=Montserrat:wght@300;400;500&family=Open+Sans:wght@300;400&display=swap">
<style>
:root{
  --brand-blue:#1a4fae;
  --panel-blue:#0b4fc0;
  --panel-dark:#2d3347;
  --white:#ffffff;
  --ink:#333842;
  --ink-soft:#5b606a;
  --rule:#d4d6da;
  --icon-bg:#e3e4e6;
  --sky-top:#4f87a5;
  --sky-mid:#9fb9c4;
  --sun:#e8d7aa;
}
*{margin:0;padding:0;box-sizing:border-box}
html,body{width:1089px;height:1200px;overflow:hidden;background:var(--white)}
body{position:relative;font-family:"Open Sans",sans-serif;color:var(--ink)}
.hero{position:absolute;left:0;top:0;width:1089px;height:518px;overflow:hidden}
.hero-photo{position:absolute;inset:0;
  background:
    linear-gradient(115deg,rgba(255,240,205,.85) 0%,rgba(232,215,170,.45) 30%,rgba(0,0,0,0) 55%),
    linear-gradient(90deg,rgba(0,0,0,0) 48%,#6d5a4a 62%,#4b3f36 100%),
    linear-gradient(180deg,var(--sky-top) 0%,var(--sky-mid) 55%,#c8a873 100%)}
.brand{position:absolute;left:116px;top:28px;display:flex;align-items:center;gap:12px}
.brand-mark{width:48px;height:48px;background:var(--brand-blue)}
.brand-name{font-family:"Montserrat",sans-serif;font-weight:500;font-size:34px;letter-spacing:1px;color:var(--brand-blue);line-height:1}
.main-nav{position:absolute;top:46px;left:536px;display:flex;gap:34px}
.main-nav a{font-family:"Montserrat",sans-serif;font-size:14px;color:var(--white);text-decoration:none;letter-spacing:.3px}
.hero-title{position:absolute;left:120px;top:240px;font-family:"Montserrat",sans-serif;font-weight:300;color:var(--white);line-height:1}
.hero-title .line-1{display:block;font-size:39px}
.hero-title .line-2{display:block;font-size:52px;margin-top:12px}
.slider-dots{position:absolute;left:500px;top:477px;display:flex;gap:4px}
.slider-dots span{width:16px;height:16px;border-radius:50%;background:var(--white)}
.slider-dots span.active{background:transparent;border:2px solid var(--white)}
.feature{position:absolute;top:518px;width:545px;height:368px;text-align:center;color:var(--white);overflow:hidden}
.feature-bio{left:0;background:linear-gradient(135deg,#1560c8 0%,var(--panel-blue) 50%,#0a45a8 100%)}
.feature-projects{left:545px;width:544px;background:linear-gradient(135deg,#454a5c 0%,var(--panel-dark) 45%,#6a5a5a 80%,#a07d6e 100%)}
.feature-projects::after{content:"";position:absolute;inset:0;background:linear-gradient(180deg,rgba(0,0,0,0) 50%,rgba(20,22,35,.6) 100%)}
.feature-inner{position:relative;z-index:1;padding-top:108px}
.feature h2{font-family:"Montserrat",sans-serif;font-weight:400;font-size:30px;letter-spacing:.5px}
.feature p{width:400px;margin:16px auto 0;font-size:13.4px;line-height:23px}
.btn{display:inline-block;margin-top:18px;border:2px solid var(--white);padding:8px 14px 7px 15px;font-family:"Montserrat",sans-serif;font-size:13px;color:var(--white);text-decoration:none}
.btn svg{margin-left:4px;vertical-align:-1px}
.footer-col{position:absolute;top:928px}
.footer-col h3{font-family:"Montserrat",sans-serif;font-weight:400;font-size:20px;color:var(--ink)}
.footer-col ul{list-style:none;margin-top:12px}
.footer-col li{font-family:"Montserrat",sans-serif;font-weight:300;font-size:13.5px;color:var(--ink-soft);line-height:27px}
.col-projects{left:116px}
.col-resources{left:307px;top:931px}
.col-follow{left:508px}
.social{display:flex;gap:8px;margin-top:16px}
.social span{width:34px;height:34px;border-radius:50%;background:var(--icon-bg)}
.footer-brand{position:absolute;left:775px;top:930px;width:200px;text-align:center}
.footer-brand .brand-mark{width:62px;height:58px;margin:0 auto 14px}
.footer-brand .brand-name{font-size:27px;letter-spacing:.5px;line-height:1.15}
.footer-rule{position:absolute;left:114px;top:1123px;width:862px;height:1px;background:var(--rule)}
.legal{position:absolute;left:111px;top:1150px;font-size:12px;color:var(--ink-soft)}
.footer-nav{position:absolute;left:637px;top:1146px;display:flex;gap:31px}
.footer-nav a{font-family:"Montserrat",sans-serif;font-size:13.5px;color:var(--ink);text-decoration:none}
</style>
</head>
<body>
<header class="hero">
  <div class="hero-photo" role="img" aria-label="Photo of a modern apartment building with balconies against a sunny sky"></div>
  <div class="brand"><div class="brand-mark"></div><div class="brand-name">HALVERY</div></div>
  <nav class="main-nav"><a href="#">HOME</a><a href="#">ABOUT</a><a href="#">BIO</a><a href="#">PROJECTS</a><a href="#">CONTACT US</a></nav>
  <h1 class="hero-title"><span class="line-1">WORLD CLASS</span><span class="line-2">CONSTRUCTION</span></h1>
  <div class="slider-dots"><span class="active"></span><span></span><span></span><span></span></div>
</header>

<section class="feature feature-bio" role="img" aria-label="Blue toned photo of glass office towers">
  <div class="feature-inner">
    <h2>OUR BIO</h2>
    <p>Curabitur iaculis tempus eros Curabitur vel mi sit amet magna malesuada ultrices Ut nisi erat fermentum vel congue id euismod in elit Fusce ultricies orci ac feugiat suscipit</p>
    <a class="btn" href="#">READ MORE<svg width="7" height="10" viewBox="0 0 7 10"><path d="M0 0L7 5L0 10Z" fill="#fff"/></svg></a>
  </div>
</section>
<section class="feature feature-projects" role="img" aria-label="Dark photo of a city escalator and towers at sunset">
  <div class="feature-inner">
    <h2>PROJECTS</h2>
    <p>Curabitur iaculis tempus eros Curabitur vel mi sit amet magna malesuada ultrices Ut nisi erat fermentum vel congue id euismod in elit Fusce ultricies orci ac feugiat suscipit</p>
    <a class="btn" href="#">READ MORE<svg width="7" height="10" viewBox="0 0 7 10"><path d="M0 0L7 5L0 10Z" fill="#fff"/></svg></a>
  </div>
</section>

<footer>
  <div class="footer-col col-projects"><h3>Projects</h3><ul><li>Commercial</li><li>Residential</li><li>Community</li><li>Location Map</li></ul></div>
  <div class="footer-col col-resources"><h3>Resources</h3><ul><li>Our Team</li><li>Support</li><li>Testimonials</li></ul></div>
  <div class="footer-col col-follow"><h3>Follow Us</h3><div class="social"><span></span><span></span><span></span><span></span><span></span></div></div>
  <div class="footer-brand"><div class="brand-mark"></div><div class="brand-name">HALVERY<br>CONSTRUCTION</div></div>
  <div class="footer-rule"></div>
  <div class="legal">© 2016 Company Name &nbsp;All right reserved &nbsp;Term of Use</div>
  <nav class="footer-nav"><a href="#">Home</a><a href="#">About</a><a href="#">Bio</a><a href="#">Projects</a><a href="#">Contact us</a></nav>
</footer>
</body>
</html>
```